Custom Manufacturing Company square space website design

I own a custom manufacturing company that uses precision cutting technology to manufacture project components over a couple industries. We have an industrial CNC router and state of the art edge bander and cut a lot of cabinetry components for cabinet shops, builders, closet companies, ect. We offer design and assembly for any cabinetry or can build cabinets to spec. We also cut components for other industries out of wood, plastics, acryclics, ect. We offer design engineering services, product development protype services. we have a 3D printer farm. We want our communicate trust, dependability, and the value we place on client relationships.

We essentially want a credibility website. Landing page and drops downs for services we offer, capabilites, about us, contact

```html
<!DOCTYPE html>
<html lang="en">
<head>
<meta charset="utf-8">
<title>Northgate CNC</title>
<link href="https://fonts.googleapis.com/css2?family=Michroma&family=Roboto:wght@400;500;700&display=swap" rel="stylesheet">
<style>
:root{
  --gold:#b08a52;
  --gold-dark:#9c7842;
  --ink:#1c1c1c;
  --text:#555555;
  --light:#f1f1f1;
  --line:#d9d9d9;
  --dark:#141414;
  --white:#ffffff;
}
*{margin:0;padding:0;box-sizing:border-box}
html,body{width:1200px;height:3305px;overflow:hidden}
body{font-family:'Roboto',sans-serif;color:var(--text);background:var(--white);position:relative}
.display{font-family:'Michroma',sans-serif;font-weight:400;color:var(--ink);letter-spacing:1px}
section,header,footer{position:relative;width:1200px}
.abs{position:absolute}
.btn{position:absolute;display:flex;align-items:center;gap:10px;justify-content:center;border-radius:22px;background:var(--gold);color:var(--white);font-weight:700;font-size:15px;height:43px;text-transform:uppercase}
.btn svg{width:15px;height:15px}
p.body{font-size:14.5px;line-height:25px;text-align:justify}

/* header */
.site-header{height:91px;background:var(--white)}
.brand{position:absolute;display:flex;align-items:center;gap:10px}
.brand-mark{width:22px;height:22px;border:2px solid var(--ink)}
.brand-name{font-size:17px;font-weight:500;color:var(--ink);letter-spacing:3px}
.nav{position:absolute;left:338px;top:40px;display:flex;gap:29px;font-size:14.5px;color:#333}
.nav .active{color:var(--gold);position:relative}
.nav .active::after{content:"";position:absolute;left:0;right:0;bottom:-12px;height:3px;background:var(--gold);width:42px;margin:auto}
.call{position:absolute;left:888px;top:26px;display:flex;gap:12px;align-items:center}
.call small{display:block;font-size:13.5px;color:#222}
.call strong{display:block;font-size:20px;color:#222;font-weight:700;letter-spacing:.5px}

/* hero */
.hero{height:601px;background:linear-gradient(100deg,#d9d2c6 0%,#efe9df 30%,#c9bca7 55%,#8d8576 75%,#d6cfc4 100%)}
.hero-box{left:281px;top:171px;width:638px;height:258px;background:rgba(80,80,80,.6);text-align:center}
.hero-box h1{font-family:'Michroma',sans-serif;font-weight:400;color:var(--white);font-size:43px;margin-top:36px;letter-spacing:1px;white-space:nowrap}
.hero-box p{color:var(--white);font-size:17px;line-height:28px;margin-top:14px}
.hero .btn{left:502px;top:337px;width:195px;height:48px;border-radius:24px;background:#111;font-size:16px}
.dots{left:563px;top:532px;display:flex;gap:5px}
.dots span{width:12px;height:12px;border:2px solid var(--white);border-radius:50%}
.dots span.on{background:var(--white);box-shadow:inset 0 0 0 2px #777}

/* about */
.about{height:528px;background:var(--light)}
.about-photo{left:112px;top:72px;width:495px;height:385px;background:linear-gradient(160deg,#e8e2d8,#f6f4ef 45%,#c8b9a0 70%,#efede8)}
.about h2{left:665px;top:100px;font-size:31px}
.about .copy{left:665px;top:148px;width:424px}
.about .copy p+p{margin-top:12px}
.about .btn{left:665px;top:380px;width:158px}

/* services */
.services{height:547px}
.services h2{left:0;width:1200px;text-align:center;top:92px;font-size:31px}
.card{top:169px;width:310px;height:291px;background:var(--white);box-shadow:0 2px 10px rgba(0,0,0,.15);border-radius:4px}
.card-photo{width:100%;height:227px;border-radius:4px 4px 0 0}
.card-icon{left:120px;top:192px;width:70px;height:70px;border-radius:50%;background:var(--white);display:flex;align-items:center;justify-content:center}
.card h3{position:absolute;bottom:18px;width:100%;text-align:center;font-size:17px;font-weight:500;color:#1a1a1a}

/* capabilities */
.capabilities{height:537px;background:linear-gradient(90deg,#111 0%,#1d1d1d 50%,#121212 100%)}
.capabilities h2{left:112px;top:104px;font-size:31px;color:var(--white)}
.capabilities .copy{left:112px;top:152px;width:423px;color:#e6e6e6}
.capabilities .copy p+p{margin-top:12px}
.capabilities .btn{left:112px;top:384px;width:158px}
.cap-ring{left:644px;top:65px;width:420px;height:420px;border-radius:50%;border:3px solid var(--gold);padding:10px}
.cap-photo{width:100%;height:100%;border-radius:50%;background:linear-gradient(135deg,#4a3626,#8a6a4a 40%,#e6e2dc 60%,#777 100%)}

/* contact */
.contact{height:586px}
.contact h2{left:0;width:1200px;text-align:center;top:82px;font-size:31px}
.contact h3{font-size:21px;font-weight:500;color:#333;top:162px}
.detail{left:112px;display:flex;gap:22px;align-items:flex-start}
.detail svg{width:32px;height:32px;flex:none}
.detail .label{font-size:16px;font-weight:500;color:#111;text-transform:uppercase}
.detail .val{font-size:15px;line-height:25px;color:#555}
.socials{left:114px;top:446px;display:flex;gap:8px}
.socials span{width:34px;height:34px;border-radius:50%;background:#111}
.field{position:absolute;border:1px solid var(--line);height:44px;width:249px;display:flex;align-items:center;gap:6px;padding-left:17px;font-size:12px;color:#666}
.field svg{width:11px;height:11px}
.contact .btn{left:558px;top:466px;width:159px}

/* footer */
.site-footer{height:360px;background:#000;color:var(--white)}
.footer-brand{left:112px;top:170px}
.footer-brand .brand-mark{border-color:var(--white);width:30px;height:30px}
.footer-brand .brand-name{color:var(--white);font-size:22px}
.fcol h4{font-size:16px;font-weight:700;letter-spacing:.3px}
.fcol h4::after{content:"";display:block;width:65px;height:2px;background:var(--white);margin-top:12px}
.fcol ul{list-style:none;margin-top:18px;font-size:12px}
.fcol li{height:36px}
.finfo{display:flex;gap:12px;align-items:flex-start;font-size:12px;line-height:20px;margin-top:14px}
.finfo i{width:22px;height:22px;border-radius:50%;background:#2a2a2a;flex:none}
.sub-field{left:838px;top:183px;width:252px;height:36px;border-radius:18px;background:var(--white);overflow:hidden;display:flex}
.sub-field span{flex:1;font-size:11px;color:#777;padding:12px 0 0 22px}
.sub-field b{width:48px;background:var(--gold);display:flex;align-items:center;justify-content:center}
.fsocials{left:833px;top:245px;display:flex;gap:10px}
.fsocials span{width:30px;height:30px;border-radius:50%;background:var(--white)}
.bottom-bar{height:55px;background:#141414;color:var(--white);font-size:13px}
</style>
</head>
<body>

<header class="site-header">
  <div class="brand" style="left:110px;top:34px"><span class="brand-mark"></span><span class="brand-name">NORTHGATE CNC</span></div>
  <nav class="nav">
    <span class="active">HOME</span><span>SERVICES WE OFFER</span><span>CAPABILITIES</span><span>ABOUT US</span><span>CONTACT</span>
  </nav>
  <div class="call">
    <svg width="28" height="28" viewBox="0 0 24 24" fill="none" stroke="#b08a52" stroke-width="2"><path d="M5 3h4l2 5-2.5 1.5a11 11 0 0 0 6 6L16 13l5 2v4a2 2 0 0 1-2 2A17 17 0 0 1 3 5a2 2 0 0 1 2-2z"/></svg>
    <div><small>Call Us Today!</small><strong>+1 888 888 8888</strong></div>
  </div>
</header>

<section class="hero" role="img" aria-label="Bright white kitchen with marble floor, navy island and brass pendant lights">
  <div class="abs hero-box">
    <h1>NORTHGATE CNC</h1>
    <p>Lorem ipsum dolor sit amet, consectetur adipiscing elit, sed do<br>eiusmod tempor incididunt ut labore et dolore magna aliqua.</p>
  </div>
  <div class="btn">GET STARTED <svg viewBox="0 0 16 16"><circle cx="8" cy="8" r="8" fill="#fff"/><path d="M6.5 4.5 10 8l-3.5 3.5" stroke="#111" stroke-width="2" fill="none"/></svg></div>
  <div class="abs dots"><span></span><span></span><span class="on"></span><span></span><span></span></div>
</section>

<section class="about">
  <div class="abs about-photo" role="img" aria-label="White bathroom vanity cabinets with granite countertop"></div>
  <h2 class="abs display">ABOUT US</h2>
  <div class="abs copy">
    <p class="body">Lorem ipsum dolor sit amet, consectetur adipiscing elit, sed do eiusmod tempor incididunt ut labore et dolore magna aliqua. Ut enim ad minim veniam, quis nostrud exercitation ullamco laboris nisi ut aliquip ex ea commodo consequat. Duis aute irure dolor in reprehenderit in voluptate velit esse cillum dolore</p>
    <p class="body">Exercitation ullamco laboris nisied uted aliquip exnea commodo consequat. Duis aute irure dolor in reprehenderit &nbsp;Excepteur sint occaecat cupidatat non proident sunt in culpa qui officia .</p>
  </div>
  <div class="btn">READ MORE <svg viewBox="0 0 16 16"><circle cx="8" cy="8" r="8" fill="#fff"/><path d="M6.5 4.5 10 8l-3.5 3.5" stroke="#b08a52" stroke-width="2" fill="none"/></svg></div>
</section>

<section class="services">
  <h2 class="abs display">SERVICES WE OFFER</h2>
  <div class="abs card" style="left:112px">
    <div class="card-photo" role="img" aria-label="White shaker kitchen cabinets with wood countertop" style="background:linear-gradient(135deg,#5a4636,#e9e6e1 40%,#f3f1ee 70%,#8a6b4e)"></div>
    <div class="abs card-icon"><svg width="40" height="30" viewBox="0 0 40 30"><rect x="1" y="1" width="38" height="28" rx="2" fill="#111"/><path d="M20 1v28M1 15h38" stroke="#fff" stroke-width="2"/><path d="M8 8h6M26 8h6M8 22h6M26 22h6" stroke="#fff" stroke-width="2"/></svg></div>
    <h3>Lorem ipsum dolor sit amet</h3>
  </div>
  <div class="abs card" style="left:445px">
    <div class="card-photo" role="img" aria-label="Grey painted kitchen with island and gold pendants" style="background:linear-gradient(160deg,#d8d6d2,#f1f0ec 45%,#8a919a 75%,#c5c2bb)"></div>
    <div class="abs card-icon"><svg width="36" height="36" viewBox="0 0 36 36"><rect x="2" y="2" width="32" height="32" rx="2" fill="#111"/><path d="M2 12h32M2 22h32M18 22v12" stroke="#fff" stroke-width="2"/><path d="M13 7h10" stroke="#fff" stroke-width="2"/></svg></div>
    <h3>Lorem ipsum dolor sit amet</h3>
  </div>
  <div class="abs card" style="left:778px">
    <div class="card-photo" role="img" aria-label="Installer fitting wooden upper kitchen cabinets" style="background:linear-gradient(140deg,#6b3a1e,#a0653a 40%,#d8b99a 70%,#8a5a36)"></div>
    <div class="abs card-icon"><svg width="34" height="34" viewBox="0 0 34 34"><rect x="2" y="2" width="30" height="30" rx="2" fill="#111"/><path d="M17 2v30" stroke="#fff" stroke-width="2"/><path d="M13 14v6M21 14v6" stroke="#fff" stroke-width="2"/></svg></div>
    <h3>Lorem ipsum dolor sit amet</h3>
  </div>
</section>

<section class="capabilities">
  <h2 class="abs display" style="color:#fff">CAPABILITIES</h2>
  <div class="abs copy">
    <p class="body">Lorem ipsum dolor sit amet, consectetur adipiscing elit, sed do eiusmod tempor incididunt ut labore et dolore magna aliqua. Ut enim ad minim veniam, quis nostrud exercitation ullamco laboris nisi ut aliquip ex ea commodo consequat. Duis aute irure dolor in reprehenderit in voluptate velit esse cillum dolore</p>
    <p class="body">Exercitation ullamco laboris nisied uted aliquip exnea commodo consequat. Duis aute irure dolor in reprehenderit &nbsp;Excepteur sint occaecat cupidatat non proident sunt in culpa qui officia .</p>
  </div>
  <div class="btn">READ MORE <svg viewBox="0 0 16 16"><circle cx="8" cy="8" r="8" fill="#fff"/><path d="M6.5 4.5 10 8l-3.5 3.5" stroke="#b08a52" stroke-width="2" fill="none"/></svg></div>
  <div class="abs cap-ring"><div class="cap-photo" role="img" aria-label="Hand opening a white drawer with wooden utensil organizer and plates"></div></div>
</section>

<section class="contact">
  <h2 class="abs display">CONTACT US</h2>
  <h3 class="abs" style="left:113px">Contact Details</h3>
  <h3 class="abs" style="left:558px">Get In Touch</h3>

  <div class="abs detail" style="top:220px">
    <svg viewBox="0 0 24 24"><path d="M12 2a7 7 0 0 0-7 7c0 5 7 13 7 13s7-8 7-13a7 7 0 0 0-7-7zm0 9.5A2.5 2.5 0 1 1 12 6.5a2.5 2.5 0 0 1 0 5z" fill="#111"/></svg>
    <div class="val" style="padding-left:4px">235.Lorem ipsum dolor sit ametconsectetur<br>united states</div>
  </div>
  <div class="abs detail" style="top:300px">
    <svg viewBox="0 0 24 24" fill="none" stroke="#111" stroke-width="1.4"><path d="M5 3h4l2 5-2.5 1.5a11 11 0 0 0 6 6L16 13l5 2v4a2 2 0 0 1-2 2A17 17 0 0 1 3 5a2 2 0 0 1 2-2z"/><path d="M14 3a7 7 0 0 1 7 7M14 6a4 4 0 0 1 4 4"/></svg>
    <div style="padding-left:6px"><div class="label">Phone Number</div><div class="val">401.555.0142</div></div>
  </div>
  <div class="abs detail" style="top:370px">
    <svg viewBox="0 0 24 24" fill="none" stroke="#111" stroke-width="1.4"><rect x="2" y="5" width="20" height="14"/><path d="m2 5 10 8 10-8M2 19l7-7M22 19l-7-7"/></svg>
    <div style="padding-left:4px"><div class="label">Email</div><div class="val">daniel@northgatemillwork.com</div></div>
  </div>
  <div class="abs socials" aria-label="Social links"><span></span><span></span><span></span></div>

  <div class="field" style="left:558px;top:217px"><svg viewBox="0 0 12 12" fill="none" stroke="#666"><circle cx="6" cy="4" r="2.5"/><path d="M1.5 11.5a4.5 4.5 0 0 1 9 0"/></svg>Name</div>
  <div class="field" style="left:838px;top:217px"><svg viewBox="0 0 12 12"><path d="M2 1h3l1 3-1.5 1a6 6 0 0 0 3 3L8.5 6.5l3 1v3A1.5 1.5 0 0 1 10 12 10 10 0 0 1 0 2 1.5 1.5 0 0 1 2 1z" fill="#666"/></svg>Phone Number</div>
  <div class="field" style="left:558px;top:275px"><svg viewBox="0 0 12 12" fill="none" stroke="#666"><rect x=".5" y="2.5" width="11" height="7"/><path d="m.5 2.5 5.5 4 5.5-4"/></svg>Email Address</div>
  <div class="field" style="left:838px;top:275px"><svg viewBox="0 0 12 12"><path d="M8.5 1 11 3.5 4 10.5 1 11l.5-3z" fill="#666"/></svg>Subject</div>
  <div class="field" style="left:558px;top:332px;width:528px;height:86px;align-items:flex-start;padding-top:30px"><svg viewBox="0 0 12 12" fill="none" stroke="#666"><ellipse cx="6" cy="5.5" rx="5.5" ry="4"/></svg>Messagge</div>
  <div class="btn">SUBMIT NOW <svg viewBox="0 0 16 16"><circle cx="8" cy="8" r="8" fill="#fff"/><path d="M6.5 4.5 10 8l-3.5 3.5" stroke="#b08a52" stroke-width="2" fill="none"/></svg></div>
</section>

<footer class="site-footer">
  <div class="brand footer-brand"><span class="brand-mark"></span><span class="brand-name">NORTHGATE CNC</span></div>

  <div class="abs fcol" style="left:411px;top:80px">
    <h4>QUICK LINKS</h4>
    <ul><li>Home</li><li>Services We Offer</li><li>Capabilities</li><li>About Us</li><li>Contact</li></ul>
  </div>

  <div class="abs fcol" style="left:579px;top:80px;width:220px">
    <h4>CONTACT US</h4>
    <div class="finfo" style="margin-top:22px"><i></i><span style="padding-top:1px">+1 888 888 8888</span></div>
    <div class="finfo"><i></i><span style="padding-top:1px">info@northgatecnc.com</span></div>
    <div class="finfo"><i></i><span>235.Lorem ipsum dolor sit amet<br>consectetur united states</span></div>
    <div class="finfo"><i></i><span style="padding-top:1px">123.456.7890</span></div>
  </div>

  <div class="abs fcol" style="left:832px;top:80px;width:260px">
    <h4>SUBSCRIBE TO OUR BLOG</h4>
    <p style="font-size:12px;line-height:21px;margin-top:18px;padding-left:5px">Sign up today to get resources on how to<br>attract and retain more customers!</p>
  </div>
  <div class="abs sub-field"><span>Email Address</span><b><svg width="16" height="16" viewBox="0 0 16 16"><path d="M15 1 1 7l5 2 2 6z" fill="#fff"/></svg></b></div>
  <div class="abs fsocials" aria-label="Social links"><span></span><span></span><span></span></div>
</footer>

<div class="bottom-bar" style="position:relative;width:1200px">
  <span class="abs" style="left:111px;top:19px">Copyright© 2023 &nbsp;<u>Northgate CNC</u> &nbsp;| &nbsp;All Rights Reserved</span>
  <span class="abs" style="left:843px;top:19px">Terms and Conditions &nbsp;&nbsp;| &nbsp;&nbsp;Privacy Policy</span>
  <span class="abs" style="left:1131px;top:21px;font-size:11px">C47</span>
</div>

</body>
</html>
```